Property management company looking for modern card design

We at Blue Heron Partners provides property management services for its residential and commercial properties, with expertise in all categories of multifamily, industrial and office projects throughout California.

We need a business card design that is professional and modern designed business card. In our field, clients get hundreds of business cards, we would like our card to stand out.

Please avoid small print.

Target Market(s)

Professionals and high end clients

Industry/Entity Type

Financial Planning

Contact Information for Business Card

Company Name: Blue Heron Partners, Name, email, license #, phone number, website blueheronpartners.com

Font styles to use
Sans Serif

Requirements
Must have
• The card design needs to be adaptable because there is a possibly we will be expanding into different sectors other than real estate. The card design should be focused on financial planning and asset management.
Nice to have
• Modern and simple business card. Eye catching. Non-standard size/shaped cards would be great.
• blueheronpartners.com
Should not have
• Too many bright color or any pictures or shapes of real estate stuff.

```html
<!DOCTYPE html>
<html lang="en">
<head>
<meta charset="utf-8">
<title>Blue Heron Partners – Business Card</title>
<link href="https://fonts.googleapis.com/css2?family=Open+Sans:wght@400;600;700&display=swap" rel="stylesheet">
<style>
  :root {
    --page: #ecebe8;
    --kraft-light: #c6a57a;
    --kraft: #b8936a;
    --kraft-dark: #a9845b;
    --ink: #141210;
    --shadow: rgba(0, 0, 0, 0.22);
  }
  * { box-sizing: border-box; margin: 0; padding: 0; }
  html, body {
    width: 1200px;
    height: 900px;
    overflow: hidden;
    background: var(--page);
    font-family: "Open Sans", Arial, sans-serif;
    color: var(--ink);
  }
  .canvas { position: relative; width: 1200px; height: 900px; }
  .card {
    position: absolute;
    overflow: hidden;
    background:
      radial-gradient(circle at 30% 25%, var(--kraft-light), transparent 60%),
      linear-gradient(135deg, var(--kraft) 0%, var(--kraft-dark) 100%);
    box-shadow: 0 8px 24px var(--shadow);
  }
  .card--front { left: 238px; top: 60px; width: 555px; height: 345px; }
  .card--back { left: 459px; top: 518px; width: 559px; height: 342px; }

  .holder { position: absolute; left: 30px; top: 55px; }
  .holder__name { font-weight: 700; font-size: 16px; line-height: 20px; }
  .holder__title { font-size: 13.5px; line-height: 18px; }

  .license { position: absolute; left: 30px; top: 185px; font-size: 14px; }
  .license__label { font-weight: 700; }

  .contacts { position: absolute; left: 30px; top: 218px; list-style: none; }
  .contacts li {
    display: flex; align-items: center; gap: 8px;
    font-size: 14px; line-height: 20px;
  }
  .contacts svg { width: 11px; height: 11px; fill: var(--ink); flex: none; }

  .brand-disc {
    position: absolute; left: 249px; top: 18px;
    width: 306px; height: 306px; border-radius: 50%;
    background: var(--ink);
  }

  .wordmark {
    position: absolute; left: 0; right: 0; top: 128px;
    text-align: center;
    font-weight: 400; font-size: 34px; letter-spacing: 1px;
    text-transform: uppercase;
  }
</style>
</head>
<body>
<main class="canvas">
  <section class="card card--front">
    <div class="holder">
      <p class="holder__name">Daniel Harper</p>
      <p class="holder__title">Managing Director</p>
    </div>
    <p class="license"><span class="license__label">License:</span> BHP01245</p>
    <ul class="contacts">
      <li>
        <svg viewBox="0 0 24 24" aria-hidden="true"><path d="M6.6 10.8a15.1 15.1 0 0 0 6.6 6.6l2.2-2.2a1 1 0 0 1 1-.25 11.4 11.4 0 0 0 3.6.57 1 1 0 0 1 1 1V20a1 1 0 0 1-1 1A17 17 0 0 1 3 4a1 1 0 0 1 1-1h3.5a1 1 0 0 1 1 1c0 1.25.2 2.45.57 3.6a1 1 0 0 1-.25 1z"/></svg>
        044-555 201 384
      </li>
      <li>
        <svg viewBox="0 0 24 24" aria-hidden="true"><path d="M2 5h20v14H2z M2 5l10 8 10-8" /></svg>
        info@blueheronpartners.com
      </li>
      <li>
        <svg viewBox="0 0 24 24" aria-hidden="true"><circle cx="12" cy="12" r="10"/></svg>
        www.blueheronpartners.com
      </li>
    </ul>
    <div class="brand-disc" aria-hidden="true"></div>
  </section>

  <section class="card card--back">
    <p class="wordmark">Blue Heron Partners</p>
  </section>
</main>
</body>
</html>
```